Web design project for exciting Australian start-up

Background
We are looking for a creative and talented web design artist to work alongside our market leading web developer.
• You will be required to create a modern and clean design theme for our website, incorporating selected rustic colour scheme elements for our exciting Australian start-up to operate within the coffee industry.
reoccurring work to be expected to flow to the successful designer.
Requirements
• c. 5 - 10 page website
• Landing page
• Log in/ out
• 404 template
• Typography is emphasised
• Please use either a) typemarrow.com, b) free web fonts, c) brindle fonts
• All design elements in vector format
• Preferably with icons for each header title(i.e. about us, how it works etc) but designer have free reign over how the site looks, so might not be applicable
• All pages to be responsive
• Down to eSlab resolution

High level visual design brief attached - additional pages to be worked from base design.

Design inspiration
• We would like to use design elements from the following sources:
http://www.zandrix.com/halcyon/ (Functionality)
Colour scheme refer to logo and complementary style guide

```html
<!DOCTYPE html>
<html lang="en">
<head>
<meta charset="utf-8">
<title>Roast Quarter — Coffee Marketplace</title>
<link rel="stylesheet" href="https://fonts.googleapis.com/css2?family=Roboto+Condensed:wght@400;700&family=Mr+Dafoe&family=Arimo:wght@400&display=swap">
<style>
  :root{
    --header-top:#c27016;
    --header-bottom:#d48a2b;
    --nav-text:#fff6e6;
    --headline-orange:#f39a4c;
    --headline-red:#e8474a;
    --script-white:#ffffff;
    --button-top:#e0861f;
    --button-bottom:#c66d10;
    --footer-bg:#1b1a19;
    --footer-head:#f0913d;
    --footer-link:#bdb8b2;
    --logo-dark:#2a1a0c;
    --logo-muted:#8a8681;
    --slider-bg:#7c2a18;
  }
  *{margin:0;padding:0;box-sizing:border-box}
  html,body{width:1200px;height:795px;overflow:hidden;background:var(--footer-bg)}
  body{position:relative;font-family:"Arimo",Arial,sans-serif}

  .site-header{position:absolute;left:0;top:0;width:1200px;height:81px;
    background:linear-gradient(to bottom,var(--header-top),var(--header-bottom))}
  .brand{position:absolute;left:171px;top:22px;display:flex;align-items:center;gap:8px;
    font-family:"Roboto Condensed",sans-serif;font-weight:700;font-size:24px;letter-spacing:1px;color:var(--logo-dark)}
  .brand-mark{width:34px;height:34px;border-radius:50%;background:var(--logo-dark)}
  .main-nav{position:absolute;top:33px;left:0;font-size:13px;color:var(--nav-text)}
  .main-nav a{position:absolute;white-space:nowrap;color:inherit;text-decoration:none}

  .hero{position:absolute;left:0;top:81px;width:1200px;height:552px;
    background:
      radial-gradient(ellipse 420px 230px at 830px 390px,#c99a62 0%,#8a5a2c 40%,rgba(60,30,10,0) 100%),
      radial-gradient(ellipse 700px 260px at 500px 560px,#6b3f1c 0%,rgba(40,20,8,0) 100%),
      #050302}
  .headline{position:absolute;left:105px;font-family:"Roboto Condensed",sans-serif;line-height:1}
  .headline-main{top:134px;font-size:74px;color:var(--headline-orange)}
  .headline-sub{top:214px;font-size:47px;color:var(--headline-red)}
  .headline-script{left:112px;top:262px;font-family:"Mr Dafoe",cursive;font-size:72px;color:var(--script-white)}

  .watch-button{position:absolute;left:113px;top:373px;width:198px;height:58px;border-radius:3px;
    background:linear-gradient(to bottom,var(--button-top),var(--button-bottom));
    display:flex;align-items:center;padding-left:24px;gap:14px;
    font-family:"Roboto Condensed",sans-serif;font-size:21px;color:#fff;letter-spacing:-.5px;text-decoration:none}

  .slider-controls{position:absolute;left:945px;top:475px;display:flex;gap:2px}
  .slider-controls span{width:41px;height:41px;background:var(--slider-bg);opacity:.85;display:flex;align-items:center;justify-content:center}

  .site-footer{position:absolute;left:0;top:633px;width:1200px;height:162px;background:var(--footer-bg)}
  .footer-col{position:absolute;top:27px}
  .footer-col h3{font-family:"Roboto Condensed",sans-serif;font-weight:400;font-size:18px;color:var(--footer-head);margin-bottom:5px}
  .footer-col a{display:block;font-size:11px;line-height:20.6px;color:var(--footer-link);text-decoration:none;padding-left:2px}
  .footer-brand{position:absolute;left:777px;top:34px;display:flex;align-items:center;gap:7px;
    font-family:"Roboto Condensed",sans-serif;font-weight:700;font-size:17px;letter-spacing:1px;color:var(--logo-muted)}
  .footer-brand .brand-mark{width:28px;height:28px;background:var(--logo-muted)}
  .copyright{position:absolute;left:783px;top:78px;font-size:11px;line-height:20.6px;color:var(--footer-link)}
</style>
</head>
<body>
  <header class="site-header">
    <div class="brand"><span class="brand-mark"></span>ROAST QUARTER</div>
    <nav class="main-nav">
      <a href="#" style="left:617px">Login</a>
      <a href="#" style="left:702px">Helpful info</a>
      <a href="#" style="left:820px">How we are</a>
      <a href="#" style="left:941px">Join us now</a>
    </nav>
  </header>

  <section class="hero" role="img" aria-label="Steaming cup of coffee on a saucer with roasted beans scattered over hessian sacking, dark background">
    <h1 class="headline headline-main">AUSTRALIA’S</h1>
    <p class="headline headline-sub">FIRST ONLINE</p>
    <p class="headline headline-script">Coffee Marketplace</p>
    <a class="watch-button" href="#">WATCH VIDEO
      <svg width="24" height="24" viewBox="0 0 24 24"><circle cx="12" cy="12" r="12" fill="#f4e6d4"/><path d="M10 7l5 5-5 5" fill="none" stroke="#c66d10" stroke-width="2.6" stroke-linecap="round" stroke-linejoin="round"/></svg>
    </a>
    <div class="slider-controls">
      <span><svg width="14" height="22" viewBox="0 0 14 22"><path d="M12 1L2 11l10 10" fill="none" stroke="#c98a78" stroke-width="1.5"/></svg></span>
      <span><svg width="14" height="22" viewBox="0 0 14 22"><path d="M2 1l10 10L2 21" fill="none" stroke="#c98a78" stroke-width="1.5"/></svg></span>
    </div>
  </section>

  <footer class="site-footer">
    <div class="footer-col" style="left:173px">
      <h3>HELPFUL INFO</h3>
      <a href="#">About us</a><a href="#">Media enquiries</a><a href="#">Terms &amp; conditions</a><a href="#">Privacy policy</a>
    </div>
    <div class="footer-col" style="left:387px">
      <h3>WHO WE ARE</h3>
      <a href="#">How it works</a><a href="#">FAQ</a><a href="#">Contact us</a>
    </div>
    <div class="footer-col" style="left:585px">
      <h3>JOIN US ON</h3>
      <a href="#">Chatterbook</a><a href="#">Chirper</a><a href="#">WorkLink</a><a href="#">ViewTube</a>
    </div>
    <div class="footer-brand"><span class="brand-mark"></span>ROAST QUARTER</div>
    <p class="copyright">Copyright © 2014 Roast Quarter.<br>All rights reserved.</p>
  </footer>
</body>
</html>
```